BRAMBLEFORD CONSTRUCTIONS B-Card

I currently have a b-card design but will be removing the image (tree) from the logo and have text only.
I want the card to be classy and strong within the building and construction industry.
I will be using Spot UV on the cards as per the attached examples. I will also send through some sketched ideas that I have in mind.
The color blue is similar to the image (No. 6) attached images

Target Market(s)

middle to maturre aged.
Home Owners / Renovators and Builders

Industry/Entity Type

Construction

Contact Information for Business Card

BRAMBLEFORD CONSTRUCTIONS
Name: Gareth Pennick
Title: Project Manager
Mobile: 0427 351 804
Office: (08) 9316 5172
Address: 47C Corvell Street, Kestrelford KT 6102
Email: info@bramblefordhomes.com.au
PO Box: 3817 Kestrelford KT 6105

Colors
0592cd
33a6d7
85cae6
1b1b1b

Requirements
Must have
• 1. It must have spot UV on the front of card, maybe back of card too
• 2. I really like the blue on image 6. (or at least a really cool electric blue against the charcoal grey background)
• 3. The font must be slimline and modern. Easy to read
• 4. There must be no black used on the card... Only greys and dark charcoal greys
• 5. Use only the text from the logo "Brambleford Constructions" Not the image of the tree. I am wanting the b-cards to be more masculine.
Nice to have
• 1. I like the design concept on image 6. but happy to see what else you can do with the Spot UV
• 2. Unless you have a really cool idea of the image of the tree (from previous logo) Spot UV somewhere in the design concept thats original and different then I am keen to see what you come up with
• 3. Try changing the color of the logo eg. full white or Blue and white
• 4. Another option is to have the Brambleford Logo on the front of card with the spot UV in the background of text which we specialise in eg, Roofing, Ceiling, Insulation, Gutter Guards, Electrical, Insurance etc and we can add or reduce items as required. Similar to image 12.
Should not have
• Do not include the image of the tree from previous logo. unless you have a really cool idea of Spot UV somewhere in the design concept thats original and different.

```html
<!DOCTYPE html>
<html lang="en">
<head>
<meta charset="utf-8">
<title>Brambleford Constructions – Business Card</title>
<link rel="stylesheet" href="https://fonts.googleapis.com/css2?family=Open+Sans:wght@400;600;700&display=swap">
<style>
  :root {
    --electric-blue: #1f9ad6;
    --card-blue: #2ea4d9;
    --card-blue-light: #4fb6e3;
    --card-blue-deep: #1689c4;
    --charcoal: #1b1b1b;
    --stage: #141414;
    --text-grey: #4a4a4a;
    --paper: #ffffff;
  }
  * { margin: 0; padding: 0; box-sizing: border-box; }
  html, body {
    width: 1200px;
    height: 900px;
    overflow: hidden;
    background: var(--stage);
    font-family: "Open Sans", Arial, sans-serif;
  }
  .canvas { position: relative; width: 1200px; height: 900px; }

  .card {
    position: absolute;
    top: 306px;
    width: 440px;
    height: 271px;
    border-radius: 12px;
    overflow: hidden;
  }
  .card--front { left: 149px; background: var(--paper); }
  .card--back { left: 608px; background: var(--card-blue); }

  /* Wordmark */
  .wordmark { position: absolute; font-weight: 700; line-height: 1; }
  .wordmark__name { display: block; letter-spacing: -0.5px; white-space: nowrap; }
  .wordmark__sub { display: block; font-weight: 400; white-space: nowrap; }

  .card--front .wordmark { left: 29px; top: 33px; color: var(--electric-blue); }
  .card--front .wordmark__name { font-size: 25.5px; }
  .card--front .wordmark__sub { font-size: 10.5px; letter-spacing: 7.4px; margin-top: 3px; padding-left: 2px; }

  /* Contact block */
  .contact { position: absolute; left: 219px; top: 95px; color: var(--text-grey); font-size: 12px; line-height: 16px; }
  .contact__name { color: var(--electric-blue); font-size: 14.5px; font-weight: 600; line-height: 18px; }
  .contact__title { margin-bottom: 12px; }
  .contact__address { margin-bottom: 10px; }
  .contact__address strong { font-weight: 700; color: #3a3a3a; }
  .contact__line { display: flex; align-items: center; gap: 6px; }
  .contact__line svg { width: 9px; height: 11px; fill: var(--electric-blue); flex: none; }

  /* Back */
  .spot-uv-art {
    position: absolute; inset: 0;
    background: radial-gradient(ellipse at 50% 45%, var(--card-blue-light) 0%, var(--card-blue) 55%, var(--card-blue-deep) 100%);
  }
  .card--back .wordmark {
    left: 0; right: 0; top: 104px; text-align: center; color: var(--paper);
  }
  .card--back .wordmark__name { font-size: 44px; }
  .card--back .wordmark__sub { font-size: 16.5px; letter-spacing: 13.6px; margin-top: 8px; padding-left: 13.6px; }
</style>
</head>
<body>
<main class="canvas">

  <section class="card card--front" aria-label="Business card front">
    <div class="wordmark">
      <span class="wordmark__name">BRAMBLEFORD</span>
      <span class="wordmark__sub">CONSTRUCTIONS</span>
    </div>

    <div class="contact">
      <p class="contact__name">Gareth Pennick</p>
      <p class="contact__title">Project Manager</p>
      <p class="contact__address">47C Corvell Street,<br>Kestrelford KT 6102<br><strong>PO Box:</strong> 3817 Kestrelford KT 6105</p>
      <p class="contact__line">
        <svg viewBox="0 0 9 11" aria-hidden="true"><path d="M2 0h5a1 1 0 0 1 1 1v9a1 1 0 0 1-1 1H2a1 1 0 0 1-1-1V1a1 1 0 0 1 1-1zm0 1.5v7h5v-7z"/></svg>
        0427 351 804
      </p>
      <p class="contact__line">
        <svg viewBox="0 0 9 11" aria-hidden="true"><path d="M1.6 1.2 3 .6l1.3 2.3-1 .8c.4 1.4 1.3 2.6 2.4 3.3l.9-.8 2 1.6-.8 1.3c-.4.6-1.2.8-1.9.5C3.3 8.3 1.1 5.4.9 2.6c0-.6.2-1.1.7-1.4z"/></svg>
        (08) 9316 5172
      </p>
    </div>
  </section>

  <section class="card card--back" aria-label="Business card back">
    <div class="spot-uv-art" role="img" aria-label="Spot UV tree with branches and leaves spread across the blue card"></div>
    <div class="wordmark">
      <span class="wordmark__name">BRAMBLEFORD</span>
      <span class="wordmark__sub">CONSTRUCTIONS</span>
    </div>
  </section>

</main>
</body>
</html>
```